Heron Haulage needs Bussiness cards!

Our new trucking company needs business cards!
We need the same design with two different names and emails, everything else it's the same.
I have included our original logo so we can use it for the design.
Note: the logo to be used is the o e with the buffalo on the right side, next to the letters H and H.

Target Market(s)

Trucking, refrigerated transportation, freight

Industry/Entity Type

Business

Contact Information for Business Card

Card #1:
Marcus Whitfield
marcuswhitfield@heronhaulage.example
1-855-317-6094
(956)238-7160
4117 W. Larkin Ave.
Pharr, TX 78590
www.heronhaulage.example

Card#2:
Rosalba Quintero
rosalba@heronhaulage.example
1-855-317-6094
(956)238-7160
4117 W. Larkin Ave.
Pharr, TX 78590
www.heronhaulage.example

Font styles to use
Sans Serif

Colors
0655a3
ec1f27
ffffff

Requirements
Must have
• our logo
Nice to have
• roads on background,

```html
<!DOCTYPE html>
<html lang="en">
<head>
<meta charset="utf-8">
<title>Heron Haulage – Business Card</title>
<link href="https://fonts.googleapis.com/css2?family=Open+Sans:wght@400;600;800&display=swap" rel="stylesheet">
<style>
  :root {
    --stage: #000000;
    --paper: #ffffff;
    --navy: #143261;
    --navy-deep: #0c2a55;
    --blue: #0655a3;
    --red: #c8202e;
    --glow-red: #9c1f35;
  }
  * { margin: 0; padding: 0; box-sizing: border-box; }
  html, body {
    width: 1200px; height: 900px; overflow: hidden;
    background: var(--stage);
    font-family: "Open Sans", Arial, sans-serif;
  }
  .canvas { position: relative; width: 1200px; height: 900px; }

  .card {
    position: absolute; top: 275px;
    width: 477px; height: 293px; overflow: hidden;
  }
  .card--front {
    left: 116px; background: var(--paper);
    border-radius: 0 46px 0 46px;
  }
  .card--back {
    left: 622px;
    border-radius: 46px 0 46px 0;
    background:
      radial-gradient(ellipse 150px 90px at 230px 70px, rgba(176,32,52,.85), rgba(176,32,52,0) 100%),
      radial-gradient(ellipse 220px 150px at 420px 30px, rgba(6,85,163,.6), rgba(6,85,163,0) 100%),
      linear-gradient(180deg, #2a3566 0%, var(--navy-deep) 60%, #0b2c58 100%);
  }

  .brand {
    position: absolute; display: flex; align-items: center; gap: 12px;
    font-weight: 800; letter-spacing: -0.5px; white-space: nowrap;
  }
  .brand__mark { border-radius: 50%; flex: none; }
  .card--front .brand { left: 36px; top: 42px; font-size: 38px; color: var(--navy); }
  .card--front .brand__mark { width: 44px; height: 44px; background: var(--navy); }
  .card--back .brand { left: 102px; top: 116px; font-size: 36px; color: var(--paper); }
  .card--back .brand__mark { width: 40px; height: 40px; background: var(--paper); }

  .name-rule {
    position: absolute; left: 0; right: 0; top: 158px;
    display: flex; align-items: center;
  }
  .name-rule__line { height: 2px; background: var(--red); }
  .name-rule__line--long { flex: 1; }
  .name-rule__line--short { width: 13px; }
  .person {
    padding: 0 6px; font-size: 17px; font-weight: 600; color: var(--navy); white-space: nowrap;
  }
  .person__last { color: var(--red); }

  .contacts {
    position: absolute; right: 20px; top: 173px;
    list-style: none; text-align: right;
    font-size: 12.5px; color: var(--navy);
  }
  .contacts li {
    display: flex; justify-content: flex-end; align-items: center;
    gap: 5px; height: 19.7px;
  }
  .contacts svg { width: 10px; height: 10px; fill: var(--red); flex: none; }
  .address {
    position: absolute; right: 21px; top: 256px;
    font-size: 12.5px; color: var(--navy);
  }
</style>
</head>
<body>
<div class="canvas">

  <section class="card card--front" aria-label="Business card front">
    <div class="brand"><span>Heron Haulage</span><span class="brand__mark"></span></div>

    <div class="name-rule">
      <span class="name-rule__line name-rule__line--long"></span>
      <span class="person">Marcus <span class="person__last">Whitfield</span></span>
      <span class="name-rule__line name-rule__line--short"></span>
    </div>

    <ul class="contacts">
      <li>1-855-317-6094
        <svg viewBox="0 0 24 24" aria-hidden="true"><path d="M6.6 10.8a15.1 15.1 0 0 0 6.6 6.6l2.2-2.2c.3-.3.7-.4 1-.2 1.1.4 2.3.6 3.6.6.6 0 1 .4 1 1V20c0 .6-.4 1-1 1A17 17 0 0 1 3 4c0-.6.4-1 1-1h3.5c.6 0 1 .4 1 1 0 1.3.2 2.5.6 3.6.1.3 0 .7-.2 1z"/></svg>
      </li>
      <li>(956)238-7160
        <svg viewBox="0 0 24 24" aria-hidden="true"><path d="M7 1h10a2 2 0 0 1 2 2v18a2 2 0 0 1-2 2H7a2 2 0 0 1-2-2V3a2 2 0 0 1 2-2zm0 3v14h10V4zm5 15.5a1.2 1.2 0 1 0 0 2.4 1.2 1.2 0 0 0 0-2.4z"/></svg>
      </li>
      <li>marcuswhitfield@heronhaulage.example
        <svg viewBox="0 0 24 24" aria-hidden="true"><path d="M2 5h20v14H2zm2 2v.4l8 5.2 8-5.2V7zm0 2.8V17h16V9.8l-8 5.2z"/></svg>
      </li>
      <li>www.heronhaulage.example
        <svg viewBox="0 0 24 24" aria-hidden="true"><circle cx="12" cy="12" r="10"/></svg>
      </li>
    </ul>
    <p class="address">4117 W. Larkin Ave. Pharr, TX 78590</p>
  </section>

  <section class="card card--back" aria-label="Business card back">
    <div class="brand"><span>Heron Haulage</span><span class="brand__mark"></span></div>
  </section>

</div>
</body>
</html>
```